THE VELVET ORBIT FASHION RE-BRAND

I am having a re-brand of The Velvet Orbit brand to include the website look and feel, and corporate identity.

The brand is defined by its minimal architectural and edgy products and contemporary feel. It is now moving into a slightly more glamorous and higher end market and price point and the branding and look and feel needs to reflect that.

Website Pages

1) Creative and striking artistic Landing page featuring
- main images - slideshow
- other images of collections
- optionalVideo/Sound - Fashion Film
- Instagram Feed

Lookbook/Collections page featuring pictures from fashion weeks of each collection
Press Page
About Page
Product Page
Information Page

The existing website isnt terrible but it needs more stying and a more polished artistic and upmarket feeling without losing its clean and contemporary feeling. This may be achieved using borders or touch of colours or other small detail that will bring everything together.

The existing logo is the just the name which is fine but I am looking for another logo to stand with it which will be a symbol or a repeating pattern using colours black white grey and silver.
Updates

Hi All Here is some website copy for the About Page The Brand Story I want somewhere on the landing page as a scrollable graphic. see quillharbour.com/about/ The rest of it - About Us and Design Ethos will go on a seperte page. Thanks see below text Text for Landing Page We are London. We are every cool city in the world. We are New York, Paris, Berlin. We are directional. We lead. We are freedom seekers. We aspire. We are full of contradictions …...and potential. We experiment. We dont want to be limited ….or labelled. We are strivers and dreamers. We self start. We get it on our own. We are travellers and taste makers. We are bosses and business women. We are creatives and professionals. We are logical and intelligent and loving. We read and see and know. We stand out. We are unique. We are loyal. We are all about our people. We stand true. We love art design and beautiful interesting things. We have to feel it. We have never ending lists. We live music. We explore every emotional terrain within and without. Our Story We created The Velvet Orbit to speak to the woman who has as Velvet Orbit as she does passions. We speak to those that are frustrated at being boxed in - we know you, we see you, that woman that can be feminine and edgy, urban and elegant, bold and understated, glamorous yet minimal. Our brand speaks to that multifaceted woman, you, and is a perfect mash-up of all of her sides. This is a new way to dress for our times We created this for those who appreciate fashion as a living art an important and vital mode of expression. We wanted to help women feel more free, more expressive and more than ever able to communicate all of their moods, all of their gifts through the medium of wearable but exciting contemporary urban luxury. We keep things simple but ever changing. Our clothes are versatile yet inspired. That are what you need for your lifestyle and allows you to be all of the women you are. We give you room to constantly evolve and expand their boundaries and experience new emotional terrain through the themes and moods of every new collection. We are a London bred brand, but are not afraid to explore many moods - the soft and feminine but also the dark and edgy - even if they appear contradictory. Ultimately we want to leave you with a wardrobe of collectible pieces that will provide you in years to come with your life's fashion soundtrack, markers made out of fabric of all your life's memories and milestones. Our vision throughout is to allow you to experience and express your Velvet Orbit through beautiful fashion. Design Ethos We like beautiful clothes that are well made fit well are distinctive but incredibly wearable. We are Made in England and take quality fabric and finishing seriously. We make clothes that uniquely combine urban edge with feminine elegance and a luxe understated glamour. We have a signature but we challenge ourselves with every new collection to find new emotional terrain connect with a new part of our journey communicate a mood or experience that moves us feel around a concept/ Today we may be dark, tomorrow light. We are inspired by everything art, culture, politics, and feeling.Everything that touches your life becomes part of our work. Experimentation is the whole point and why we do this. We aim to delight and challenge you. Get you to try something new. Maybe even feel something new. We want to talk to you through fashion. Stay connected @thevelvetorbit

Target Market(s)

25 year old women.

Industry/Entity Type

Fashion

Contact Information for Business Card

Nadia Corvell
Creative Director
nadia@thevelvetorbit.com

Nadia Corvell
Creative Director
nadia@thevelvetorbit.com
07812366905

Logo Text

No text only a symbol

Number of Pages Required

5+ page

Font styles to use
Sans Serif

Colors

Designer to choose colors to be used in the design.

Requirements
Must have
• My standard colours are grey black and white (see existing webpage) and so to bring in a glamour quotient one idea is use of metallics such as silver or neon.
Nice to have
• to tie the stationary and web together with the logo - same colours and themes - repeating symbols or patterns.

```html
<!DOCTYPE html>
<html lang="en">
<head>
<meta charset="utf-8">
<title>The Velvet Orbit</title>
<link href="https://fonts.googleapis.com/css2?family=Mulish:wght@400;600;700;800&display=swap" rel="stylesheet">
<style>
:root{
  --bg:#efe6e3;
  --white:#ffffff;
  --blush:#e0b9ad;
  --accent:#c5573d;
  --ink:#3a3332;
  --muted:#6f6563;
  --faint:#e6d3cd;
}
*{margin:0;padding:0;box-sizing:border-box}
html,body{width:1200px;height:5014px;overflow:hidden}
body{background:var(--bg);font-family:"Mulish",sans-serif;color:var(--ink);position:relative}
.abs{position:absolute}
.photo{position:absolute;display:block}

/* sidebar */
.sidebar{left:0;top:0;width:268px;height:608px;background:var(--white);padding:28px 22px}
.brand{font-size:20px;font-weight:600;letter-spacing:1px;color:var(--ink);border-bottom:2px solid var(--ink);display:inline-block;padding-bottom:4px;white-space:nowrap}
.cart{position:absolute;top:104px;left:22px;font-size:15px;color:var(--accent)}
.nav-main{position:absolute;top:162px;left:22px;list-style:none}
.nav-main li{font-size:15px;font-weight:600;letter-spacing:1px;height:40px}
.nav-sub{position:absolute;top:314px;left:22px;list-style:none}
.nav-sub li{font-size:14px;color:var(--muted);height:30px}
.social{position:absolute;top:438px;left:22px;display:flex;gap:18px}
.social span{width:10px;height:10px;border-radius:50%;background:var(--ink);display:block}
.currency{position:absolute;top:492px;left:22px;font-size:14px;color:var(--muted)}
.copyright{position:absolute;top:540px;left:22px;font-size:12px;color:var(--muted);line-height:24px}

/* hero */
.hero{left:287px;top:10px;width:903px;height:598px}
.hero-title{left:287px;top:222px;width:903px;text-align:center;color:var(--white);font-size:40px;font-weight:800;line-height:48px}
.btn-light{position:absolute;left:680px;top:336px;width:120px;height:42px;background:var(--white);color:var(--ink);font-size:14px;font-weight:700;display:flex;align-items:center;justify-content:center;letter-spacing:.5px}
.dots{left:610px;top:576px;display:flex;gap:10px}
.dots span{width:80px;height:4px;background:rgba(255,255,255,.45)}
.dots span:first-child{background:var(--white)}

/* intro band */
.intro{left:287px;top:618px;width:903px;height:301px;background:var(--blush);text-align:center;padding-top:70px}
.intro h2{font-size:38px;font-weight:800;color:var(--ink)}
.intro p{font-size:15px;line-height:24px;color:var(--muted);width:620px;margin:16px auto 0}
.link{font-size:15px;color:var(--accent);letter-spacing:.5px;display:inline-flex;align-items:center;gap:8px}
.intro .link{margin-top:22px}

/* products */
.caption{position:absolute;background:var(--white);font-size:12px;font-weight:600;height:32px;line-height:32px;padding:0 14px;white-space:nowrap}

/* testimonial */
.quote-mark{left:640px;top:2290px;width:200px;text-align:center;font-size:240px;font-weight:800;color:var(--faint);line-height:1}
.quote{left:370px;top:2352px;width:740px;text-align:center;font-size:17px;line-height:27px;color:var(--muted)}
.quote-author{left:370px;top:2478px;width:740px;text-align:center;font-size:14px;color:var(--muted)}

/* video */
.video{left:287px;top:2614px;width:903px;height:462px}
.video-title{left:287px;top:2780px;width:903px;text-align:center;color:var(--white);font-size:40px;font-weight:800}

/* press */
.section-title{text-align:center;font-size:40px;font-weight:800;color:var(--ink)}
.post-title{font-size:23px;font-weight:700;text-align:center;width:415px}
.post-date{font-size:12px;text-align:center;width:415px}
.post-text{font-size:12.5px;line-height:17px;color:var(--muted);text-align:center;width:415px}

/* instagram */
.insta{left:287px;top:3888px;width:903px;height:240px;background:var(--blush);text-align:center;padding-top:70px}

/* newsletter */
.news-sub{left:0;width:1200px;top:4856px;text-align:center;font-size:16px;color:var(--ink)}
.input{left:485px;top:4891px;width:381px;height:47px;background:var(--white);border:1px solid #d9ccc8;font-size:12px;color:#a79c99;padding:0 22px;line-height:45px}
.subscribe{left:876px;top:4891px;width:117px;height:47px;background:var(--accent);color:var(--white);font-size:14px;font-weight:700;display:flex;align-items:center;justify-content:center}
</style>
</head>
<body>

<aside class="abs sidebar">
  <div class="brand">THE VELVET ORBIT</div>
  <div class="cart">Cart (0)</div>
  <ul class="nav-main"><li>COLLECTIONS</li><li>SPECIALS</li><li>GIFTS</li></ul>
  <ul class="nav-sub"><li>We are</li><li>Collections</li><li>Press</li></ul>
  <div class="social" aria-label="Social links"><span></span><span></span><span></span></div>
  <div class="currency">USD ⌄</div>
  <div class="copyright">Copyright © 2018 The Velvet Orbit<br>All rights reserved</div>
</aside>

<svg class="photo hero" role="img" aria-label="Woman in a pink coat and sunglasses in front of a brick wall" viewBox="0 0 903 598" preserveAspectRatio="none">
  <defs>
    <linearGradient id="gHero" x1="0" y1="0" x2="1" y2="0"><stop offset="0" stop-color="#7a5f54"/><stop offset=".35" stop-color="#b08478"/><stop offset=".6" stop-color="#6b5148"/><stop offset="1" stop-color="#3d302c"/></linearGradient>
    <linearGradient id="gHeroShade" x1="0" y1="0" x2="0" y2="1"><stop offset="0" stop-color="#000" stop-opacity="0"/><stop offset="1" stop-color="#000" stop-opacity=".3"/></linearGradient>
  </defs>
  <rect width="903" height="598" fill="url(#gHero)"/>
  <rect width="903" height="598" fill="url(#gHeroShade)"/>
</svg>
<div class="abs hero-title">Phasellus Consequat<br>Sagittis Suscipit</div>
<div class="btn-light">SHOP NOW</div>
<div class="abs dots"><span></span><span></span></div>

<section class="abs intro">
  <h2>Pellentesque blandit</h2>
  <p>Praesent iaculis faucibus urna sit amet lacinia. Maecenas consequat justo enim, ac mattis massa imperdiet quis. Fusce eget neque elit.</p>
  <div class="link">SHOP COLLECTION <span>⟶</span></div>
</section>

<svg class="photo" style="left:287px;top:926px;width:448px;height:639px" role="img" aria-label="Woman in white blouse and sunglasses by a brick wall" viewBox="0 0 448 639" preserveAspectRatio="none">
  <defs><linearGradient id="g1" x1="0" y1="0" x2="1" y2="1"><stop offset="0" stop-color="#7d4a37"/><stop offset=".55" stop-color="#d8cfc8"/><stop offset="1" stop-color="#a7785f"/></linearGradient></defs>
  <rect width="448" height="639" fill="url(#g1)"/></svg>
<div class="caption" style="left:307px;top:1513px">Vestibulum condimentum - $212</div>

<svg class="photo" style="left:745px;top:926px;width:445px;height:639px" role="img" aria-label="Woman in navy polka dot dress on a city street" viewBox="0 0 445 639" preserveAspectRatio="none">
  <defs><linearGradient id="g2" x1="0" y1="0" x2="0" y2="1"><stop offset="0" stop-color="#a89a86"/><stop offset=".45" stop-color="#55576a"/><stop offset="1" stop-color="#2b2f48"/></linearGradient></defs>
  <rect width="445" height="639" fill="url(#g2)"/></svg>
<div class="caption" style="left:765px;top:1513px">Pellentesque consectetur - $262</div>

<svg class="photo" style="left:287px;top:1575px;width:448px;height:638px" role="img" aria-label="Smiling woman in beige sweater holding a coffee cup" viewBox="0 0 448 638" preserveAspectRatio="none">
  <defs><linearGradient id="g3" x1="0" y1="0" x2="0" y2="1"><stop offset="0" stop-color="#c4c2bb"/><stop offset=".55" stop-color="#b49a82"/><stop offset="1" stop-color="#8e3b33"/></linearGradient></defs>
  <rect width="448" height="638" fill="url(#g3)"/></svg>
<div class="caption" style="left:307px;top:2161px">Maecenas vel tortor - $432</div>

<svg class="photo" style="left:745px;top:1575px;width:445px;height:638px" role="img" aria-label="Woman in black leather jacket and round sunglasses" viewBox="0 0 445 638" preserveAspectRatio="none">
  <defs><linearGradient id="g4" x1="0" y1="0" x2="1" y2="0"><stop offset="0" stop-color="#e2e0de"/><stop offset=".5" stop-color="#2f2b2b"/><stop offset="1" stop-color="#d4d2d0"/></linearGradient></defs>
  <rect width="445" height="638" fill="url(#g4)"/></svg>
<div class="caption" style="left:765px;top:2161px">Aenean facilisis - $145</div>

<div class="abs quote-mark" aria-hidden="true">”</div>
<svg class="abs" style="left:290px;top:2380px" width="28" height="14" viewBox="0 0 28 14" aria-label="Previous"><path d="M27 7H3M8 2 3 7l5 5" stroke="#c5573d" stroke-width="2" fill="none"/></svg>
<svg class="abs" style="left:1162px;top:2380px" width="28" height="14" viewBox="0 0 28 14" aria-label="Next"><path d="M1 7h24M20 2l5 5-5 5" stroke="#c5573d" stroke-width="2" fill="none"/></svg>
<p class="abs quote">Vivamus efficitur ex condimentum, malesuada eros eget, feugiat nibh. Sed tellus ex, imperdiet eget gravida sit amet, volutpat eget turpis</p>
<p class="abs quote-author">Madison in New York</p>

<svg class="photo video" role="img" aria-label="Fashion film still: woman in sunglasses beside a car on a city street" viewBox="0 0 903 462" preserveAspectRatio="none">
  <defs><linearGradient id="gV" x1="0" y1="0" x2="1" y2="0"><stop offset="0" stop-color="#2e3034"/><stop offset=".45" stop-color="#6d6f72"/><stop offset=".7" stop-color="#9a9894"/><stop offset="1" stop-color="#45413e"/></linearGradient></defs>
  <rect width="903" height="462" fill="url(#gV)"/>
</svg>
<div class="abs video-title">Maecenas sed nibh</div>
<svg class="abs" style="left:698px;top:2832px" width="88" height="88" viewBox="0 0 88 88" aria-label="Play video"><circle cx="44" cy="44" r="41" stroke="#fff" stroke-width="3" fill="none"/><path d="M35 28v32l26-16z" fill="#fff"/></svg>

<h2 class="abs section-title" style="left:0;width:1200px;top:3160px">Press</h2>
<div class="abs link" style="left:0;width:1200px;top:3220px;justify-content:center">VIEW ALL POSTS <span>⟶</span></div>

<svg class="photo" style="left:304px;top:3310px;width:415px;height:334px" role="img" aria-label="Three women in summer outfits laughing on a beach" viewBox="0 0 415 334" preserveAspectRatio="none">
  <defs><linearGradient id="gP1" x1="0" y1="0" x2="0" y2="1"><stop offset="0" stop-color="#d9d2cb"/><stop offset=".5" stop-color="#b99278"/><stop offset="1" stop-color="#d6bfa6"/></linearGradient></defs>
  <rect width="415" height="334" fill="url(#gP1)"/></svg>
<h3 class="abs post-title" style="left:304px;top:3662px">Quisque blandit elit tincidunt</h3>
<div class="abs post-date" style="left:304px;top:3714px">MAR 20, 2018</div>
<p class="abs post-text" style="left:304px;top:3752px">Mauris suscipit felis id nunc elementum varius. Praesent elementum nulla sit amet justo pellentesque scelerisque. Nam et tortor in ante iaculis porttitor in luctus mi.</p>

<svg class="photo" style="left:759px;top:3310px;width:415px;height:334px" role="img" aria-label="Three views of a woman in a white dress on a light background" viewBox="0 0 415 334" preserveAspectRatio="none">
  <defs><linearGradient id="gP2" x1="0" y1="0" x2="1" y2="0"><stop offset="0" stop-color="#e9e9e9"/><stop offset=".5" stop-color="#cfcdcb"/><stop offset="1" stop-color="#e6e6e6"/></linearGradient></defs>
  <rect width="415" height="334" fill="url(#gP2)"/></svg>
<h3 class="abs post-title" style="left:759px;top:3662px">Vivamus gravida sem pretium</h3>
<div class="abs post-date" style="left:759px;top:3714px">MAR 20, 2018</div>
<p class="abs post-text" style="left:759px;top:3752px">Mauris suscipit felis id nunc elementum varius. Praesent elementum nulla sit amet justo pellentesque scelerisque. Nam et tortor in ante iaculis porttitor in luctus mi.</p>

<section class="abs insta">
  <h2 class="section-title">Instagram</h2>
  <div class="link" style="margin-top:10px">▣ VIEW ALL <span>⟶</span></div>
</section>

<svg class="photo" style="left:287px;top:4139px;width:298px;height:297px" role="img" aria-label="Woman in black top and denim shorts" viewBox="0 0 10 10" preserveAspectRatio="none"><defs><linearGradient id="i1" x1="0" y1="0" x2="0" y2="1"><stop offset="0" stop-color="#dcd9d5"/><stop offset="1" stop-color="#a9a7a6"/></linearGradient></defs><rect width="10" height="10" fill="url(#i1)"/></svg>
<svg class="photo" style="left:595px;top:4139px;width:291px;height:297px" role="img" aria-label="Woman in pink dress on pink background" viewBox="0 0 10 10" preserveAspectRatio="none"><defs><linearGradient id="i2" x1="0" y1="0" x2="0" y2="1"><stop offset="0" stop-color="#efc9c4"/><stop offset="1" stop-color="#df7c82"/></linearGradient></defs><rect width="10" height="10" fill="url(#i2)"/></svg>
<svg class="photo" style="left:896px;top:4139px;width:294px;height:297px" role="img" aria-label="Woman in white top with black bag" viewBox="0 0 10 10" preserveAspectRatio="none"><defs><linearGradient id="i3" x1="0" y1="0" x2="0" y2="1"><stop offset="0" stop-color="#efedea"/><stop offset="1" stop-color="#cfc9c3"/></linearGradient></defs><rect width="10" height="10" fill="url(#i3)"/></svg>
<svg class="photo" style="left:287px;top:4446px;width:298px;height:294px" role="img" aria-label="Woman in blue jacket sitting" viewBox="0 0 10 10" preserveAspectRatio="none"><defs><linearGradient id="i4" x1="0" y1="0" x2="0" y2="1"><stop offset="0" stop-color="#e4e6ec"/><stop offset="1" stop-color="#a9b2c8"/></linearGradient></defs><rect width="10" height="10" fill="url(#i4)"/></svg>
<svg class="photo" style="left:595px;top:4446px;width:291px;height:294px" role="img" aria-label="Woman in floral dress" viewBox="0 0 10 10" preserveAspectRatio="none"><defs><linearGradient id="i5" x1="0" y1="0" x2="0" y2="1"><stop offset="0" stop-color="#b98a72"/><stop offset="1" stop-color="#5b3b3a"/></linearGradient></defs><rect width="10" height="10" fill="url(#i5)"/></svg>
<svg class="photo" style="left:896px;top:4446px;width:294px;height:294px" role="img" aria-label="Woman in striped top against yellow wall" viewBox="0 0 10 10" preserveAspectRatio="none"><defs><linearGradient id="i6" x1="0" y1="0" x2="1" y2="0"><stop offset="0" stop-color="#e3a84a"/><stop offset="1" stop-color="#b9782c"/></linearGradient></defs><rect width="10" height="10" fill="url(#i6)"/></svg>

<h2 class="abs section-title" style="left:0;width:1200px;top:4800px">Newsletter</h2>
<p class="abs news-sub">Phasellus blandit quam a ipsum gravida dapibus</p>
<div class="abs input">Enter your email address</div>
<div class="abs subscribe">SUBSCRIBE</div>

</body>
</html>
```